Homepage for the brisk-find Web Application

At the end of this text, you will find a link to a website that is under construction for a webApp that I intend to launch soon. The contest goal is for you to make redesign the homepage in a nice, fresh, modern Style. Only design, no coding necessary. It needs to have a responsive version for small screens like smart phones. Attached is the text for it, and some images that you may use. You are welcome to find or create additional supporting images. You can use PixTrove.example or similar service to find new images as long as I can purchase the non-exclusive use rights for the images at similar prices. The contest is just for the home page. However, the winner, if I like the work and we can agree on a fair price, could be contracted on a one-on-one basis to do the rest of the site. You are welcome to suggest minor changes like font sizes and minor variations on the Header banner, but that banner is consistent with the user interface of the application therefore should not change too much. The information should flow somewhat continually without much use of side bars or things like that.
https://www.brisk-find.example
Sincerely,
Marco D. Ferral

```html
<!DOCTYPE html>
<html lang="en">
<head>
<meta charset="utf-8">
<title>Brisk-Find — Find any document or item instantly</title>
<link rel="stylesheet" href="https://fonts.googleapis.com/css2?family=Poppins:wght@400;500;600&display=swap">
<style>
:root{
  --blue:#3b80d4;
  --blue-dark:#1f6cb8;
  --orange:#ff7f5a;
  --ink:#111111;
  --text:#222222;
  --mist:#dcfbfd;
  --teal:#3dbfc9;
  --white:#ffffff;
  --footer:#000000;
}
*{margin:0;padding:0;box-sizing:border-box}
html,body{width:1200px;height:3571px;overflow:hidden}
body{position:relative;background:var(--white);font-family:"Poppins",sans-serif;color:var(--text)}
.abs{position:absolute}

/* header */
.topbar{left:0;top:0;width:1200px;height:68px;background:var(--blue)}
.brand{left:97px;top:16px;display:flex;align-items:center;gap:8px;color:var(--white);font-size:22px;font-weight:400}
.brand-dot{width:28px;height:28px;border-radius:50%;background:var(--white)}
.field{top:21px;height:29px;border-radius:15px;background:var(--white);font-size:12px;color:#555;padding:7px 17px}
.field-user{left:298px;width:302px}
.field-pass{left:636px;width:304px}
.login{left:1005px;top:21px;width:98px;height:29px;border:2px solid var(--orange);border-radius:15px;color:var(--orange);font-size:13px;text-align:center;line-height:25px}
.navbar{left:0;top:68px;width:1200px;height:26px;background:var(--blue-dark)}
.nav-link{top:73px;font-size:12px;color:var(--white)}

/* shared */
.accent{color:var(--orange)}
.btn{display:block;border-radius:17px;font-size:12px;text-align:center;line-height:33px}
.btn-solid{background:var(--orange);color:var(--white)}
.btn-line{border:2px solid var(--orange);color:var(--orange);line-height:29px}
.art{border-radius:24px}
.blob{left:0;top:0}

/* hero */
.hero-title{left:97px;top:172px;font-size:50px;font-weight:600;line-height:69px;color:var(--ink)}
.hero-copy{left:97px;top:328px;width:465px;font-size:15px;line-height:26px}
.art-hero{left:721px;top:150px;width:360px;height:367px;background:linear-gradient(160deg,#9fe6ec,var(--teal));}

/* why */
.why-title{left:0;top:600px;width:1200px;text-align:center;font-size:36px;font-weight:600;line-height:51px;color:var(--ink)}
.art-paper{left:205px;top:758px;width:270px;height:330px;background:linear-gradient(160deg,#bff2f5,var(--teal) 55%,var(--orange))}
.sub-title{font-size:26px;font-weight:600;color:var(--ink)}
.paper-title{left:577px;top:755px}
.paper-copy{left:577px;top:803px;width:525px;font-size:13.5px;line-height:24.2px}

/* objects */
.objects-title{left:137px;top:1270px}
.objects-copy{left:137px;top:1323px;width:440px;font-size:13.5px;line-height:24px}
.acc-list{left:137px;top:1397px;width:456px;list-style:none}
.acc-item{height:42px;margin-bottom:15px;border-radius:21px;background:var(--white);box-shadow:0 2px 8px rgba(0,0,0,.13);display:flex;align-items:center;justify-content:space-between;padding:0 22px 0 26px;font-size:13.5px}
.acc-plus{color:var(--orange);font-size:20px;font-weight:400}
.art-objects{left:748px;top:1328px;width:319px;height:404px;background:linear-gradient(160deg,#c7f5f7,var(--teal) 60%,var(--orange))}

/* alternative */
.art-wine{left:205px;top:1954px;width:248px;height:370px;background:linear-gradient(160deg,#bff2f5,var(--teal) 55%,var(--orange))}
.alt-title{left:607px;top:1995px;font-size:36px;font-weight:600;line-height:49px;color:var(--ink)}
.alt-copy{left:607px;top:2124px;width:432px;font-size:13.5px;line-height:24.2px}
.btn-start{left:607px;top:2292px;width:123px}

/* reasons */
.reasons-title{left:0;top:2410px;width:1200px;text-align:center;font-size:36px;font-weight:600;color:var(--ink)}
.reasons{list-style:none;font-size:17.5px;line-height:24px;color:var(--ink)}
.reasons li{position:relative;padding-left:42px;margin-bottom:12px}
.reasons svg{position:absolute;left:0;top:3px}
.reasons-left{left:95px;top:2522px;width:470px}
.reasons-right{left:637px;top:2522px;width:475px}
.btn-trial{left:502px;top:2735px;width:194px;height:39px;line-height:39px;border-radius:20px;font-size:17px;box-shadow:0 4px 10px rgba(255,127,90,.35)}

/* footer */
.footer{left:0;top:2816px;width:1200px;height:47px;background:var(--footer);color:var(--white);font-size:13.5px;text-align:center;line-height:47px}
</style>
</head>
<body>

<svg class="abs blob" width="1200" height="2500" viewBox="0 0 1200 2500" aria-hidden="true">
  <path fill="var(--mist)" d="M0 615 C60 630 110 680 130 740 C150 810 170 760 330 740 C430 728 470 830 440 940 C410 1060 330 1150 200 1180 C110 1200 60 1250 0 1268 Z"/>
  <path fill="var(--mist)" d="M1200 1245 C1130 1240 1080 1300 1010 1350 C930 1410 840 1460 830 1570 C820 1690 900 1710 1000 1720 C1080 1730 1050 1840 1120 1880 C1160 1900 1185 1900 1200 1898 Z"/>
  <path fill="var(--mist)" d="M0 1795 C60 1800 100 1860 110 1920 C120 1980 250 1990 360 2000 C470 2010 500 2110 470 2200 C440 2300 330 2360 180 2380 C100 2392 50 2430 0 2446 Z"/>
</svg>

<header>
  <div class="abs topbar"></div>
  <div class="abs brand"><span class="brand-dot"></span>Brisk Find</div>
  <div class="abs field field-user">Username</div>
  <div class="abs field field-pass">Password</div>
  <div class="abs login">login</div>
  <nav>
    <div class="abs navbar"></div>
    <a class="abs nav-link" style="left:325px">About</a>
    <a class="abs nav-link" style="left:385px">Pricing</a>
    <a class="abs nav-link" style="left:453px">Blog</a>
    <a class="abs nav-link" style="left:508px">FAQs</a>
    <a class="abs nav-link" style="left:567px">Support</a>
    <a class="abs nav-link" style="left:643px">Reviews</a>
    <a class="abs nav-link" style="left:718px">Contact Us</a>
    <a class="abs nav-link" style="left:815px">Free-Trial</a>
  </nav>
</header>

<section class="hero">
  <h1 class="abs hero-title">Find any document or<br>item <span class="accent">instantly!</span></h1>
  <p class="abs hero-copy">Brisk-Find is a system that allows you to quickly search for the location of every item that you store or file. It is an essential tool for keeping track of paper documents or any other kind of physical item.</p>
  <a class="abs btn btn-solid" style="left:97px;top:459px;width:115px">Get Pricing</a>
  <a class="abs btn btn-line" style="left:238px;top:459px;width:114px">Free Trial</a>
  <div class="abs art art-hero" role="img" aria-label="Illustration of a man filing folders in a laptop shaped as a drawer cabinet"></div>
</section>

<section class="why">
  <h2 class="abs why-title">Why use a storage management system<br>like <span class="accent">Brisk-Find?</span></h2>
  <div class="abs art art-paper" role="img" aria-label="Illustration of a man carrying a large binder out of a phone drawer"></div>
  <h3 class="abs sub-title paper-title">Managing paper documents</h3>
  <p class="abs paper-copy">It is quite common for most people and businesses to receive a variety of such documents that need to be filed. The problem is how to efficiently do it in a way that any of it can easily be found, even in a distant future. We normally put them in folders on file drawers sorted by some criteria. But which criterion is the right standard for all kinds of documents? There is no right criterion for every kind of document. It is necessary to use a combination of them. If after some time you do not remember which criterion you used to file a document, you may have a hard time finding it, or not find it at all. This problem is greatly intensified when the person looking for the document is not the same person that filed it. It is estimated that workers spend over 20% of their time managing documents. A storage management system like Brisk-Find would allow any authorized user to instantly find any document regardless of who filed it or which criterion was used, as long as it was properly filed using the system.</p>
</section>

<section class="objects">
  <h3 class="abs sub-title objects-title">Managing any non-document objects</h3>
  <p class="abs objects-copy">The same is true of storing any other kind of objects. Common examples include</p>
  <ul class="abs acc-list">
    <li class="acc-item">Storage boxes, closets, warehouses, and shelves<span class="acc-plus">+</span></li>
    <li class="acc-item">Books<span class="acc-plus">+</span></li>
    <li class="acc-item">Wines<span class="acc-plus">+</span></li>
    <li class="acc-item">Safety boxes<span class="acc-plus">+</span></li>
    <li class="acc-item">Moving boxes<span class="acc-plus">+</span></li>
    <li class="acc-item">Test samples<span class="acc-plus">+</span></li>
    <li class="acc-item">Audio, video, data, and removable media<span class="acc-plus">+</span></li>
    <li class="acc-item">Keys<span class="acc-plus">+</span></li>
  </ul>
  <div class="abs art art-objects" role="img" aria-label="Illustration of a man holding a test tube beside a phone drawer"></div>
</section>

<section class="alternative">
  <div class="abs art art-wine" role="img" aria-label="Illustration of a man holding a wine bottle beside a phone drawer"></div>
  <h2 class="abs alt-title">Alternative uses for<br><span class="accent">Brisk-Find</span></h2>
  <p class="abs alt-copy">How many times have you gone to a restaurant and couldn’t recall how good (or bad) each of the dishes were that you previously ordered? You can use Brisk-Find to record each one to improve your experience for every visit. Our app can also help you decide where you want to go or which dish to recommend when you have a special occasion.</p>
  <a class="abs btn btn-solid btn-start">Get Started</a>
</section>

<section class="reasons-block">
  <h2 class="abs reasons-title">Why <span class="accent">Brisk-Find?</span></h2>
  <ul class="abs reasons reasons-left">
    <li><svg width="26" height="20" viewBox="0 0 26 20"><path d="M2 10 L10 17 L24 3" fill="none" stroke="var(--orange)" stroke-width="4" stroke-linecap="round" stroke-linejoin="round"/></svg>It is extremely easy to use.</li>
    <li><svg width="26" height="20" viewBox="0 0 26 20"><path d="M2 10 L10 17 L24 3" fill="none" stroke="var(--orange)" stroke-width="4" stroke-linecap="round" stroke-linejoin="round"/></svg>It’s very affordable. Checkout our pricing plans!</li>
    <li><svg width="26" height="20" viewBox="0 0 26 20"><path d="M2 10 L10 17 L24 3" fill="none" stroke="var(--orange)" stroke-width="4" stroke-linecap="round" stroke-linejoin="round"/></svg>Since it is online, your data is available almost anywhere in the world.</li>
  </ul>
  <ul class="abs reasons reasons-right">
    <li><svg width="26" height="20" viewBox="0 0 26 20"><path d="M2 10 L10 17 L24 3" fill="none" stroke="var(--orange)" stroke-width="4" stroke-linecap="round" stroke-linejoin="round"/></svg>It Adapts to your stile. Since each catalog can have 1 or more levels of depth (folders and sub-folders), Brisk-Find does not force you to use a specific filing or storage methodology.</li>
    <li><svg width="26" height="20" viewBox="0 0 26 20"><path d="M2 10 L10 17 L24 3" fill="none" stroke="var(--orange)" stroke-width="4" stroke-linecap="round" stroke-linejoin="round"/></svg>Data encryption ensures that your information is always private, safe, and secure.</li>
  </ul>
  <a class="abs btn btn-solid btn-trial">30 Days Free Trial</a>
</section>

<footer class="abs footer">© Copyright 2021 Brisk-find .All Rights Reserved.</footer>

</body>
</html>
```